Velmora Systems Website

Website design for our company: Velmora Systems.
The website should look fresh and IT focused. Please have a look at http://www.velmorasystems.example.au/ for our current design. We want something fresh and new, professional looking, in WordPress so we can easily make changes.

It Company

```html
<!DOCTYPE html>
<html lang="en">
<head>
<meta charset="utf-8">
<title>Velmora Systems</title>
<link href="https://fonts.googleapis.com/css2?family=PT+Sans:wght@400;700&family=Arimo:wght@400;700&display=swap" rel="stylesheet">
<style>
:root{
  --blue:#0b67c2;
  --green:#12a84b;
  --heading-blue:#1a6fc0;
  --grey-band:#c9c9c9;
  --light-band:#f2f2f2;
  --text:#333;
  --footer:#1c1c1c;
  --footer-text:#cfcfcf;
  --rule:#bdbdbd;
}
*{margin:0;padding:0;box-sizing:border-box}
html,body{width:1148px;height:1200px;overflow:hidden;background:#fff}
body{position:relative;font-family:"Arimo",Arial,sans-serif;color:var(--text)}
.abs{position:absolute}

/* header */
.brand{left:170px;top:22px;width:150px;height:70px;display:flex;align-items:center;gap:8px}
.brand-mark{width:22px;height:22px;background:var(--green);flex:none}
.brand-name{font-family:"PT Sans",sans-serif;font-weight:700;font-size:20px;color:var(--green);line-height:1.05}
.phone{right:164px;top:26px;display:flex;align-items:center;gap:6px;font-family:"PT Sans",sans-serif;font-weight:700;font-size:20px;color:#111}
.search{left:809px;top:68px;width:178px;height:26px;border:1px solid #ccc;font-size:11px;font-style:italic;color:#555;padding:6px 8px}
.search svg{position:absolute;right:6px;top:5px}

/* hero */
.band{left:0;top:112px;width:1148px;height:358px;background:var(--grey-band)}
.nav{left:160px;top:112px;width:828px;height:38px;background:var(--blue);display:flex}
.nav a{font-family:"PT Sans",sans-serif;font-size:14px;color:#fff;text-decoration:none;display:flex;align-items:center;justify-content:center;border-right:1px solid #2a7fd0;height:100%}
.nav a.active{background:var(--green)}
.hero{left:160px;top:150px;width:828px;height:364px;background:linear-gradient(100deg,#3c4a5e 0%,#6a7a8e 35%,#c9d2dd 65%,#eef1f5 100%)}
.hero-arrow{top:284px;width:36px;height:36px;border-radius:50%;background:#1b1b1b;border:3px solid rgba(255,255,255,.35);display:flex;align-items:center;justify-content:center}
.caption{left:160px;top:470px;width:828px;height:44px;background:rgba(36,104,165,.92);color:#fff;font-family:"PT Sans",sans-serif;font-size:23px;text-align:center;line-height:44px}

/* sections */
.h2{font-family:"PT Sans",sans-serif;font-size:22px;color:var(--heading-blue)}
.h2 span{color:var(--green)}
.rule{height:1px;background:var(--rule)}
.about-photo{left:170px;top:581px;width:243px;height:112px;background:linear-gradient(90deg,#c7b7a8,#7c8390 50%,#dfe3e8);border:1px solid #999}
.body-text{font-size:10.2px;line-height:16px;color:#333;text-align:justify}
.more{font-size:11px;color:var(--green);font-weight:700}
.svc{left:733px;display:flex;align-items:center;gap:22px;font-family:"PT Sans",sans-serif;font-size:17px;color:#222}
.svc svg{width:30px;height:28px}

.light-band{left:0;top:808px;width:1148px;height:160px;background:var(--light-band)}
.client{top:890px;font-family:"PT Sans",sans-serif;font-weight:700;font-size:20px;color:#555}
.code-input{left:729px;top:876px;width:244px;height:25px;border:1px solid #ccc;background:#fff;font-size:10.5px;font-style:italic;color:#666;padding:6px 10px}
.connect{left:729px;top:909px;width:88px;height:21px;background:var(--green);color:#fff;font-family:"PT Sans",sans-serif;font-size:13px;text-align:center;line-height:21px}

/* footer */
.footer{left:0;top:968px;width:1148px;height:198px;background:var(--footer)}
.fh{font-family:"PT Sans",sans-serif;font-size:14px;font-weight:400;color:#eee;top:983px}
.links{left:169px;top:1005px;width:115px;list-style:none}
.links li{font-size:10.5px;color:var(--footer-text);height:20.3px;line-height:20px;border-bottom:1px solid #3d3d3d;padding-left:14px;position:relative}
.links li:last-child{border-bottom:none}
.links li::before{content:"";position:absolute;left:2px;top:7px;border:3px solid transparent;border-left:4px solid #aaa}
.vline{width:1px;background:#3a3a3a;top:995px;height:150px}
.quote{left:324px;top:1007px;width:276px;font-size:10.6px;line-height:15.3px;color:#bdbdbd}
.cite{left:324px;top:1100px;width:273px;text-align:right;font-size:10.8px;font-weight:700;color:#999;line-height:14px}
.ci{left:652px;display:flex;gap:10px;align-items:flex-start;font-size:10.5px;color:#ddd;line-height:14px}
.ci-icon{width:19px;height:19px;border-radius:50%;background:var(--blue);flex:none;display:flex;align-items:center;justify-content:center}
.social{top:1010px;width:26px;height:26px;border-radius:50%;background:#3a3a3a}
.social.on{background:var(--green)}
.foot-brand{left:849px;top:1062px;width:129px;height:63px;border:2px solid var(--green);display:flex;align-items:center;justify-content:center;gap:7px}
.foot-brand .brand-name{font-size:15px}
.foot-brand .brand-mark{width:14px;height:14px}
.bottom{left:0;top:1166px;width:1148px;height:34px;background:var(--blue);color:#fff;font-size:10.5px;text-align:center;line-height:34px}
</style>
</head>
<body>

<header>
  <div class="abs brand"><span class="brand-mark"></span><span class="brand-name">Velmora<br>Systems</span></div>
  <div class="abs phone">
    <svg width="20" height="20" viewBox="0 0 20 20"><circle cx="10" cy="10" r="9" fill="none" stroke="var(--blue)" stroke-width="1.5"/><path d="M7 5c-1 1-1 3 1 6s4 4 5 3l1-1-2-2-1 1c-1 0-3-2-3-3l1-1-2-3z" fill="var(--blue)"/></svg>
    012-555-0148
  </div>
  <div class="abs search">search
    <svg width="14" height="14" viewBox="0 0 14 14"><circle cx="6" cy="6" r="4.5" fill="none" stroke="#999" stroke-width="1.6"/><path d="M9.5 9.5l3.5 3.5" stroke="#999" stroke-width="2"/></svg>
  </div>
</header>

<div class="abs band"></div>
<nav class="abs nav">
  <a class="active" style="width:94px">HOME</a>
  <a style="width:121px">ABOUT US</a>
  <a style="width:113px">SERVICES</a>
  <a style="width:115px">SUPPORT</a>
  <a style="width:146px">TESTIMONIALS</a>
  <a style="width:108px">CLIENTS</a>
  <a style="width:131px;border-right:none">CONTACT US</a>
</nav>
<div class="abs hero" role="img" aria-label="Engineer with laptop working beside server racks in a data centre"></div>
<div class="abs hero-arrow" style="left:174px"><svg width="12" height="16"><path d="M9 2L3 8l6 6" stroke="#fff" stroke-width="1.6" fill="none"/></svg></div>
<div class="abs hero-arrow" style="left:939px"><svg width="12" height="16"><path d="M3 2l6 6-6 6" stroke="#fff" stroke-width="1.6" fill="none"/></svg></div>
<div class="abs caption">WE HAVE SPECIALISED ENGINEERS, TRAINED TO DO SPECIALISED WORK</div>

<section>
  <h2 class="abs h2" style="left:170px;top:538px">About <span>Velmora Systems</span></h2>
  <div class="abs rule" style="left:170px;top:570px;width:524px"></div>
  <div class="abs about-photo" role="img" aria-label="Business team meeting around a table"></div>
  <p class="abs body-text" style="left:428px;top:584px;width:261px">Velmora Systems is an Adelaide based company with a single objective - to excel in the support and service of all computer and IT needs. Our core business includes information technology consultation, equipment and software optimisation, network system and application software system construction, overall system network routine maintenance and management. We are currently</p>
  <p class="abs body-text" style="left:170px;top:700px;width:519px">supporting over 200 businesses through a variety of service level agreements and support plans. We provide a high level consulting service using the most experienced engineers at a reasonable and fair price. We believe in using a Business Value approach to every aspect of computer consulting to provide our clients with the most cost-effective solutions. We understand that no one business is the same and our IT service can be tailored to fit individual requirements.</p>
  <span class="abs more" style="left:636px;top:775px">Read More...</span>
</section>

<div class="abs" style="left:714px;top:580px;width:1px;height:170px;background:#eee"></div>

<section>
  <h2 class="abs h2" style="left:730px;top:539px">Our <span>Services</span></h2>
  <div class="abs rule" style="left:730px;top:570px;width:249px"></div>
  <div class="abs svc" style="top:583px"><svg viewBox="0 0 30 28"><path d="M4 24L20 8M8 4l6 6M22 20l5 5" stroke="#333" stroke-width="3" fill="none"/></svg>ON-SITE SERVICE</div>
  <div class="abs svc" style="top:623px"><svg viewBox="0 0 30 28"><rect x="2" y="3" width="20" height="14" fill="none" stroke="#333" stroke-width="2"/><path d="M8 22h10" stroke="#333" stroke-width="2"/><circle cx="22" cy="19" r="6" fill="#fff" stroke="#333" stroke-width="2"/></svg>REMOTE DESKTOP</div>
  <div class="abs svc" style="top:665px"><svg viewBox="0 0 30 28"><path d="M4 4v8a6 6 0 0012 0V4M10 18v4a4 4 0 008 0v-6" stroke="#333" stroke-width="2" fill="none"/><circle cx="24" cy="8" r="4" fill="none" stroke="#333" stroke-width="2"/></svg>MEDICAL IT SERVICE</div>
  <div class="abs svc" style="top:706px"><svg viewBox="0 0 30 28"><rect x="2" y="3" width="20" height="15" fill="none" stroke="#333" stroke-width="2"/><path d="M5 14l5-5 4 3 5-5" stroke="#333" stroke-width="1.5" fill="none"/><circle cx="22" cy="20" r="4" fill="#fff" stroke="#333" stroke-width="2"/><path d="M25 23l3 3" stroke="#333" stroke-width="2"/></svg>PHARMACY IT SERVICE</div>
  <div class="abs svc" style="top:746px"><svg viewBox="0 0 30 28"><rect x="2" y="5" width="22" height="15" fill="none" stroke="#333" stroke-width="2"/><path d="M9 25h8M13 20v5M10 14l4 2 12-14" stroke="#333" stroke-width="2" fill="none"/></svg>WEBSITE DESIGN</div>
  <span class="abs more" style="left:927px;top:775px">View All...</span>
</section>

<div class="abs light-band"></div>
<section>
  <h2 class="abs h2" style="left:169px;top:834px">Our <span>Clients</span></h2>
  <div class="abs rule" style="left:169px;top:865px;width:540px"></div>
  <svg class="abs" style="left:672px;top:843px" width="32" height="14"><path d="M6 1L1 7l5 6" stroke="#555" stroke-width="1.5" fill="none"/><path d="M24 1l5 6-5 6" stroke="var(--green)" stroke-width="1.5" fill="none"/></svg>
  <span class="abs client" style="left:170px">Quillmarsh</span>
  <span class="abs client" style="left:336px">Tessavane</span>
  <span class="abs client" style="left:504px">Orvelle</span>
  <span class="abs client" style="left:610px">Brindlecore</span>

  <h2 class="abs h2" style="left:729px;top:836px">Remote <span>Support</span></h2>
  <div class="abs rule" style="left:729px;top:865px;width:250px"></div>
  <div class="abs code-input">Enter your 6 digit code</div>
  <div class="abs connect">Connect Now</div>
</section>

<footer>
  <div class="abs footer"></div>
  <h3 class="abs fh" style="left:169px">Main Links</h3>
  <ul class="abs links"><li>Home</li><li>About Us</li><li>Services</li><li>Support</li><li>Testimonials</li><li>Clients</li><li>Contact</li></ul>
  <div class="abs vline" style="left:295px"></div>

  <h3 class="abs fh" style="left:324px">Testimonials</h3>
  <svg class="abs" style="left:575px;top:986px" width="24" height="12"><path d="M5 1L1 6l4 5M19 1l4 5-4 5" stroke="#ccc" stroke-width="1.3" fill="none"/></svg>
  <p class="abs quote">“ I have always found the team extremely helpful with their advice over the phone. They also have the ability to access our computers remotely, and can rectify most problems quite swiftly. I have no hesitation in recommending Velmora Systems for all your IT needs. ”</p>
  <p class="abs cite">Daniel Ashcroft B.Pharm<br>Harbourline Chemists, Elm Vale</p>
  <div class="abs vline" style="left:625px"></div>

  <h3 class="abs fh" style="left:652px">Contact Info</h3>
  <div class="abs ci" style="top:1012px"><span class="ci-icon"><svg width="10" height="10"><path d="M1 5l4-4 4 4v4H1z" fill="#fff"/></svg></span>218 Kestrel Road<br>Larkfield West<br>5020 Australia</div>
  <div class="abs ci" style="top:1064px"><span class="ci-icon"><svg width="10" height="10"><path d="M2 1c-1 1 0 4 2 6s5 3 6 2l-2-2-1 1C6 8 3 5 3 4l1-1z" fill="#fff"/></svg></span><span style="padding-top:3px">088-555-0172</span></div>
  <div class="abs ci" style="top:1098px"><span class="ci-icon"><svg width="11" height="8"><rect x=".5" y=".5" width="10" height="7" fill="#fff"/><path d="M.5 .5l5 4 5-4" stroke="var(--blue)" fill="none"/></svg></span><span style="padding-top:3px">help@velmora.example</span></div>
  <div class="abs vline" style="left:821px"></div>

  <h3 class="abs fh" style="left:851px">Follow Us On</h3>
  <span class="abs social on" style="left:851px" aria-label="Social profile"></span>
  <span class="abs social" style="left:883px" aria-label="Social profile"></span>
  <span class="abs social" style="left:914px" aria-label="Social profile"></span>
  <span class="abs social" style="left:945px" aria-label="Social profile"></span>
  <div class="abs foot-brand"><span class="brand-mark"></span><span class="brand-name">Velmora<br>Systems</span></div>

  <div class="abs bottom">Copyright 2014 Velmora Systems &nbsp;|&nbsp; Terms of Use &nbsp;|&nbsp; Privacy Statement &nbsp;|&nbsp; Feedback &nbsp;|&nbsp; Legal</div>
</footer>

</body>
</html>
```